Bookcover: Ways to Turn Into a Bold Pathfinder

I am publishing a super-low-cost innovation book for €4,99 on Quillmere Open Press to help everyone become a great innovator: young ambitious people without college education nor a big budget. Do you want to help me?

Brief:
Design a book cover 1600 x 2560 pixels for QOP.
Main title: Ways to Turn Into a Bold Pathfinder
Sub title: mindset - insights - skills & tools
Author: Joost ter Brakel
Design: captive, and appealing to everyone
Target Group: young ambitious people without college education

For quillmere please format the height/width ratio of 1.6:1

```html
<!DOCTYPE html>
<html lang="en">
<head>
<meta charset="utf-8">
<title>Ways to Turn Into a Bold Pathfinder — Book Cover</title>
<link rel="stylesheet" href="https://fonts.googleapis.com/css2?family=Bebas+Neue&family=Montserrat:wght@700&display=swap">
<style>
  :root {
    --page: #ffffff;
    --cover-yellow: #f9d000;
    --title-blue: #2e3192;
    --title-red: #a00000;
    --ink: #231f20;
    --art-light: #e8c400;
    --art-deep: #d9b200;
  }
  html, body {
    margin: 0;
    padding: 0;
    width: 1200px;
    height: 1200px;
    overflow: hidden;
    background: var(--page);
  }
  .canvas {
    display: block;
    width: 1200px;
    height: 1200px;
  }
  .cover-bg { fill: var(--cover-yellow); }
  .title-band { fill: var(--title-blue); }
  .title-lead {
    font-family: 'Bebas Neue', sans-serif;
    font-size: 98px;
    fill: var(--title-blue);
  }
  .title-hero {
    font-family: 'Bebas Neue', sans-serif;
    font-size: 292px;
    fill: var(--title-red);
  }
  .title-band-word {
    font-family: 'Bebas Neue', sans-serif;
    font-size: 161px;
    fill: var(--cover-yellow);
  }
  .subtitle {
    font-family: 'Bebas Neue', sans-serif;
    font-size: 40px;
    fill: var(--ink);
  }
  .author {
    font-family: 'Montserrat', sans-serif;
    font-weight: 700;
    font-size: 22px;
    letter-spacing: 1.5px;
    fill: #111111;
  }
</style>
</head>
<body>
<svg class="canvas" viewBox="0 0 1200 1200" xmlns="http://www.w3.org/2000/svg">
  <defs>
    <linearGradient id="artGradient" x1="0" y1="0" x2="0" y2="1">
      <stop offset="0" stop-color="var(--art-light)"/>
      <stop offset="1" stop-color="var(--art-deep)"/>
    </linearGradient>
  </defs>

  <g class="book-cover">
    <rect class="cover-bg" x="293" y="140" width="614" height="919"/>

    <text class="title-lead" x="334" y="250" textLength="531" lengthAdjust="spacingAndGlyphs">WAYS TO TURN INTO A</text>
    <text class="title-hero" x="334" y="466" textLength="532" lengthAdjust="spacingAndGlyphs">BOLD</text>

    <rect class="title-band" x="293" y="478" width="614" height="132"/>
    <text class="title-band-word" x="334" y="601" textLength="531" lengthAdjust="spacingAndGlyphs">PATHFINDER</text>

    <g class="cover-illustration" role="img" aria-label="Line drawing of a head in profile with a brain and a colourful light bulb inside">
      <rect x="475" y="630" width="245" height="345" rx="110" fill="url(#artGradient)"/>
    </g>

    <text class="subtitle" x="348" y="1009" textLength="504" lengthAdjust="spacingAndGlyphs">MINDSET - INSIGHTS - SKILLS &amp; TOOLS</text>
    <text class="author" x="600" y="1046" text-anchor="middle">JOOST TER BRAKEL</text>
  </g>
</svg>
</body>
</html>
```